Real Estate Webpage Design

We have an existing website: ferndaleestatecollective.com.au
We focus customised service mainly on Property Management and second-hand property sales.
We are not entirely happy about the current design and layout can stay roughly the same as the back end coding is linked to a CRM system.
We would like to see the design are more reachable to our clients and appearing.
Please check our Website Design Draft for more details.

Industry/Entity Type

Real estate Agency

Number of Pages Required

5+ page

Font styles to use
Sans Serif

Colors

Designer to choose colors to be used in the design.

```html
<!DOCTYPE html>
<html lang="en">
<head>
<meta charset="utf-8">
<title>Ferndale Property Group</title>
<link href="https://fonts.googleapis.com/css2?family=Poppins:wght@300;400;500;600&display=swap" rel="stylesheet">
<style>
:root{
  --gold:#e9bd52;
  --navy:#2c3a50;
  --ink:#1f2630;
  --text:#6b6b6b;
  --light:#f6f6f6;
  --line:#cfcfcf;
  --white:#fff;
}
*{box-sizing:border-box;margin:0;padding:0}
html,body{width:1200px;height:4170px;overflow:hidden}
body{font-family:'Poppins',sans-serif;color:var(--ink);background:var(--white);position:relative}
.abs{position:absolute}
section,header,footer{position:absolute;left:0;width:1200px}
.label{color:var(--gold);font-size:13px}
.h2{font-size:27px;font-weight:500;color:var(--ink)}
.btn{display:flex;align-items:center;justify-content:center;font-size:13px;position:absolute;white-space:nowrap}
.btn-gold{background:var(--gold);color:#fff}
.btn-navy{background:var(--navy);color:#fff}
.btn-outline{border:1.5px solid #fff;color:#fff}

/* hero */
.hero{top:0;height:640px;overflow:hidden}
.hero-photo{position:absolute;inset:0;background:linear-gradient(180deg,#9aa4ab 0%,#bcc3c8 30%,#6b7a6a 62%,#2f3e2c 100%)}
.hero-shade{position:absolute;inset:0;background:rgba(20,28,36,.35)}
.logo{position:absolute;display:flex;align-items:center;gap:12px}
.logo-mark{width:54px;height:54px;border:3px solid var(--gold)}
.logo-name{font-size:40px;font-weight:500;color:var(--gold);line-height:1}
.logo-sub{font-size:11px;letter-spacing:1.5px;color:var(--gold);margin-left:4px}
.nav{position:absolute;top:32px;left:437px;width:551px;display:flex;justify-content:space-between;font-size:13px;color:#fff;white-space:nowrap}
.nav .active{color:var(--gold)}
.hero-title{position:absolute;top:160px;width:100%;text-align:center;font-size:41px;font-weight:600;color:var(--gold)}
.hero-text{position:absolute;top:214px;left:260px;width:680px;text-align:center;font-size:13px;line-height:22px;color:#fff}
.hero-tabs{position:absolute;top:282px;left:442px;display:flex}
.hero-tabs span{width:105px;height:36px;display:flex;align-items:center;justify-content:center;font-size:13px;color:#fff;background:var(--gold)}
.hero-tabs span.on{background:var(--navy)}
.search{position:absolute;top:318px;left:219px;width:762px;height:103px;background:rgba(255,255,255,.9);border-radius:4px}
.field{position:absolute;top:20px;width:152px}
.field b{display:block;font-size:13.5px;font-weight:500;color:var(--ink);margin-bottom:8px}
.select{height:30px;border:1px solid #777;display:flex;align-items:center;justify-content:space-between;padding:0 8px;font-size:11.5px;color:#888;background:#fff;white-space:nowrap}
.search-go{position:absolute;top:52px;left:707px;width:33px;height:30px;background:var(--navy);display:flex;align-items:center;justify-content:center}

/* about */
.about{top:640px;height:469px}
.about .label{position:absolute;top:66px;left:61px}
.about .h2{position:absolute;top:90px;left:61px}
.about p{position:absolute;left:61px;width:470px;font-size:13px;line-height:22.5px;color:var(--text)}
.about-photo{position:absolute;top:14px;left:690px;width:450px;height:370px;background:linear-gradient(160deg,#c9d6e0 0%,#8ea2b3 45%,#4a5663 100%);clip-path:polygon(50px 0,100% 0,100% 100%,50px 100%,0 50%)}

/* listings */
.listings{top:1109px;height:801px;background:var(--light)}
.center{position:absolute;width:100%;text-align:center}
.tabs{position:absolute;top:141px;left:293px;display:flex;gap:22px}
.tabs span{width:106px;height:38px;display:flex;align-items:center;justify-content:center;font-size:13px;color:#fff;background:var(--navy)}
.tabs span.on{background:var(--gold)}
.card{position:absolute;top:209px;width:340px;height:463px;background:#fff;box-shadow:0 1px 4px rgba(0,0,0,.08)}
.card-photo{height:240px;position:relative}
.badge{position:absolute;top:12px;right:12px;background:var(--navy);color:#fff;font-size:12px;padding:3px 9px}
.star{position:absolute;top:12px;left:14px}
.price{position:absolute;bottom:20px;left:20px;color:#fff;font-size:16px;font-weight:500}
.arrow-l,.arrow-r{position:absolute;top:108px}
.arrow-l{left:14px}.arrow-r{right:14px}
.card h3{font-size:16.5px;font-weight:500;margin:12px 0 0 20px}
.addr{display:flex;align-items:center;gap:6px;font-size:12.5px;color:var(--ink);margin:8px 0 0 18px}
.feats{display:flex;gap:18px;margin:16px 0 0 20px;font-size:12.5px}
.feats span{display:flex;align-items:center;gap:8px}
.card h4{font-size:16px;font-weight:500;margin:18px 0 0 20px}
.when{font-size:12.5px;color:var(--gold);margin:6px 0 0 20px}
.agent{position:absolute;bottom:0;left:0;right:0;height:45px;border-top:1px solid #eee;display:flex;align-items:center;padding:0 20px;font-size:13px}
.avatar{width:28px;height:28px;background:#b9b3ac;margin-right:14px}
.tools{margin-left:auto;display:flex;gap:8px}

/* why */
.why{top:1990px;height:403px}
.why-photo{position:absolute;left:0;top:0;width:600px;height:403px;background:linear-gradient(135deg,#d8d2c8 0%,#efe9df 50%,#c4b7a4 100%)}
.why-panel{position:absolute;left:600px;top:0;width:600px;height:403px;background:var(--navy);color:#fff}
.why-panel .label{position:absolute;top:41px;left:41px}
.why-panel .h2{position:absolute;top:60px;left:41px;color:#fff}
.why-panel p{position:absolute;top:107px;left:43px;width:470px;font-size:13px;line-height:22.5px}

/* testimonial */
.testi{top:2393px;height:376px}
.testi-left{position:absolute;left:0;top:0;width:600px;height:376px;background:var(--gold);color:#fff}
.testi-left p{position:absolute;top:70px;left:88px;width:455px;text-align:center;font-size:13px;line-height:22.5px}
.quote{position:absolute;top:46px;left:64px;font-size:90px;line-height:1;opacity:.55;font-family:Georgia,serif}
.testi-left .name{position:absolute;top:254px;width:100%;text-align:center;font-size:13.5px;color:var(--ink)}
.testi-nav{position:absolute;top:294px;left:258px;display:flex;gap:30px}
.testi-right{position:absolute;left:600px;top:0;width:600px;height:376px;background:var(--light);text-align:center}

/* blog */
.blog{top:2769px;height:620px}
.post{position:absolute;top:168px;width:340px}
.post-photo{height:205px;position:relative}
.date{position:absolute;top:0;left:0;width:55px;height:55px;background:var(--gold);color:#fff;font-size:13px;line-height:17px;display:flex;flex-direction:column;align-items:center;justify-content:center}
.post h3{font-size:16.5px;font-weight:500;margin-top:15px}
.post p{font-size:13px;line-height:22px;color:var(--text);margin-top:7px}
.read{font-size:13px;color:var(--gold);margin-top:14px;display:block}

/* contact */
.contact{top:3420px;height:406px}
.map{position:absolute;left:0;top:0;width:600px;height:406px;background:linear-gradient(150deg,#eef0ec 0%,#e3e6e1 60%,#d6e3d4 100%)}
.touch{position:absolute;left:600px;top:0;width:600px;height:406px;background:var(--gold)}
.touch h2{position:absolute;top:52px;width:100%;text-align:center;font-size:27px;font-weight:500}
.input{position:absolute;height:33px;background:#fff;font-size:12px;color:#888;padding:7px 11px}

/* footer */
.footer{top:3826px;height:344px;background:var(--navy);color:#fff}
.footer h5{position:absolute;top:48px;font-size:13px;font-weight:500;color:var(--gold)}
.footer ul{position:absolute;top:82px;left:335px;list-style:none;font-size:12.5px;line-height:27px}
.footer ul li:first-child{color:var(--gold)}
.contact-line{position:absolute;left:614px;display:flex;gap:14px;font-size:12.5px;line-height:20px}
.social{position:absolute;top:82px;left:890px;display:flex;gap:15px}
.social span{width:38px;height:38px;border-radius:50%;border:1.5px solid #fff}
.social span.on{background:var(--gold);border-color:var(--gold)}
.bottom{position:absolute;top:4145px;left:0;width:1200px;height:25px;font-size:11.5px;color:var(--ink);display:flex;align-items:center;padding:0 61px;background:#fff}
.bottom .links{margin-left:auto;display:flex;gap:26px}
</style>
</head>
<body>

<header class="hero">
  <div class="hero-photo" role="img" aria-label="Photo of a modern multi-storey glass and concrete home surrounded by pine trees"></div>
  <div class="hero-shade"></div>
  <svg class="abs" style="left:0;top:0" width="1200" height="640" viewBox="0 0 1200 640"><polygon points="0,640 0,635 760,525 1200,630 1200,640" fill="#fff"/></svg>
  <div class="logo" style="top:16px;left:60px">
    <div class="logo-mark"></div>
    <div><div class="logo-name">Ferndale</div><div class="logo-sub">PropertyGroup</div></div>
  </div>
  <nav class="nav"><span class="active">Home</span><span>About Us</span><span>Leasing</span><span>Buy</span><span>Sell</span><span>Our Team</span><span>Blog</span><span>Contact Us</span></nav>
  <div class="btn btn-gold" style="top:24px;left:1012px;width:128px;height:38px;border:1.5px solid #fff">Add Properties</div>
  <h1 class="hero-title">Welcome To Ferndale Property Group</h1>
  <p class="hero-text">Lorem Ipsum is simply dummy text of the printing and typesetting industry. Lorem Ipsum has been the industry's standard dummy text ever since the 1500s, when an unknown printer</p>
  <div class="hero-tabs"><span>For Sale</span><span class="on">For Leased</span><span>For Sold</span></div>
  <form class="search">
    <div class="field" style="left:26px"><b>Categories</b><div class="select">Property Category <svg width="14" height="8"><path d="M1 1l6 6 6-6" stroke="#333" fill="none" stroke-width="1.5"/></svg></div></div>
    <div class="field" style="left:195px"><b>City</b><div class="select">Property City <svg width="14" height="8"><path d="M1 1l6 6 6-6" stroke="#333" fill="none" stroke-width="1.5"/></svg></div></div>
    <div class="field" style="left:368px"><b>Area</b><div class="select">Property Area <svg width="14" height="8"><path d="M1 1l6 6 6-6" stroke="#333" fill="none" stroke-width="1.5"/></svg></div></div>
    <div class="field" style="left:535px"><b>Rooms</b><div class="select">Rooms Number <svg width="14" height="8"><path d="M1 1l6 6 6-6" stroke="#333" fill="none" stroke-width="1.5"/></svg></div></div>
    <div class="search-go"><svg width="16" height="16"><circle cx="6.5" cy="6.5" r="5" stroke="#fff" stroke-width="1.8" fill="none"/><path d="M10 10l5 5" stroke="#fff" stroke-width="1.8"/></svg></div>
  </form>
</header>

<section class="about">
  <div class="label">About Us</div>
  <h2 class="h2">Who Is Ferndale?</h2>
  <p style="top:128px">Ferndale takes its name from a quiet fern-filled valley, buying a property is one of the most expensive expenses and important assets for people. Ferndale is a real estate company located in Gungahlin, Canberra.</p>
  <p style="top:229px">Being a portfolio sales agent and property manager, coupled with our high-profile international real estate experience, Ferndale is considered a market leader on the cutting edge with deep industry knowledge, ranging from landlord-tenant relationships, residential purchases.</p>
  <svg class="abs" style="left:652px;top:14px" width="80" height="370"><polygon points="42,0 80,0 38,185 80,370 42,370 0,185" fill="var(--gold)"/></svg>
  <div class="about-photo" role="img" aria-label="Photo of a contemporary two-storey home at dusk with glass walls and a wet driveway"></div>
</section>

<section class="listings">
  <div class="center label" style="top:50px">Our Properties</div>
  <h2 class="center h2" style="top:80px">Listings Available For Latest Property</h2>
  <div class="tabs"><span class="on">For Lease</span><span>For Lease</span><span>Open Times</span><span>Sold</span><span>Leased</span></div>

  <article class="card" style="left:60px">
    <div class="card-photo" role="img" aria-label="Photo of a modern apartment block with red balconies behind a tree" style="background:linear-gradient(160deg,#6aa1d8 0%,#c9d3dc 45%,#4f6a3a 100%)">
      <svg class="star" width="20" height="20" viewBox="0 0 24 24"><path d="M12 2l3 6.5 7 .8-5.2 4.8 1.5 7L12 17.6 5.7 21l1.5-7L2 9.3l7-.8z" fill="var(--gold)"/></svg>
      <span class="badge">On Sale</span>
      <svg class="arrow-l" width="10" height="20"><path d="M9 1L1 10l8 9" stroke="#fff" fill="none" stroke-width="1.5"/></svg>
      <svg class="arrow-r" width="10" height="20"><path d="M1 1l8 9-8 9" stroke="#fff" fill="none" stroke-width="1.5"/></svg>
      <span class="price">$369,000+</span>
    </div>
    <h3>Gungahlin</h3>
    <div class="addr"><svg width="14" height="18" viewBox="0 0 14 18"><path d="M7 17S1 10 1 6.5a6 6 0 0112 0C13 10 7 17 7 17z" stroke="var(--gold)" fill="none" stroke-width="1.3"/><circle cx="7" cy="6.5" r="2" stroke="var(--gold)" fill="none"/></svg>18/40 Wattle Street Belconnen...</div>
    <div class="feats">
      <span><svg width="20" height="14"><rect x="1" y="1" width="18" height="12" stroke="var(--gold)" fill="none" stroke-width="1.3"/><path d="M1 8h18" stroke="var(--gold)"/></svg>1</span>
      <span><svg width="20" height="16"><path d="M1 8h18v3a4 4 0 01-4 4H5a4 4 0 01-4-4zM4 8V2h4" stroke="var(--gold)" fill="none" stroke-width="1.3"/></svg>1</span>
      <span><svg width="26" height="14"><path d="M1 10V7l4-1 4-4h8l5 4 3 1v3H1z" stroke="var(--gold)" fill="none" stroke-width="1.3"/><circle cx="7" cy="11" r="2" fill="#fff" stroke="var(--gold)"/><circle cx="19" cy="11" r="2" fill="#fff" stroke="var(--gold)"/></svg>1</span>
    </div>
    <h4>Next Inspirition:</h4>
    <div class="when">Sat 21st May 9:40 Am-10:00 Am</div>
    <div class="agent"><div class="avatar" role="img" aria-label="Agent portrait"></div>Mei Lin
      <div class="tools"><svg width="18" height="18"><circle cx="9" cy="9" r="7" stroke="#333" fill="none" stroke-width="1.3"/><path d="M9 5v4l3 2" stroke="#333" fill="none" stroke-width="1.3"/></svg><svg width="18" height="18"><path d="M2 6V2h4M12 2h4v4M16 12v4h-4M6 16H2v-4M2 2l5 5M16 2l-5 5M16 16l-5-5M2 16l5-5" stroke="#333" fill="none" stroke-width="1.3"/></svg><svg width="20" height="18"><rect x="1" y="3" width="18" height="12" stroke="#333" fill="none" stroke-width="1.3"/><path d="M1 3l9 7 9-7" stroke="#333" fill="none" stroke-width="1.3"/></svg></div>
    </div>
  </article>

  <article class="card" style="left:431px">
    <div class="card-photo" role="img" aria-label="Photo of a rooftop infinity pool beside apartment towers" style="background:linear-gradient(170deg,#b8c8d4 0%,#9fb3c0 50%,#3d7fa8 80%,#8a5a3a 100%)">
      <svg class="star" width="20" height="20" viewBox="0 0 24 24"><path d="M12 2l3 6.5 7 .8-5.2 4.8 1.5 7L12 17.6 5.7 21l1.5-7L2 9.3l7-.8z" fill="var(--gold)"/></svg>
      <span class="badge">On Sale</span>
      <svg class="arrow-l" width="10" height="20"><path d="M9 1L1 10l8 9" stroke="#fff" fill="none" stroke-width="1.5"/></svg>
      <svg class="arrow-r" width="10" height="20"><path d="M1 1l8 9-8 9" stroke="#fff" fill="none" stroke-width="1.5"/></svg>
      <span class="price">$5,00,000+</span>
    </div>
    <h3>Gungahlin</h3>
    <div class="addr"><svg width="14" height="18" viewBox="0 0 14 18"><path d="M7 17S1 10 1 6.5a6 6 0 0112 0C13 10 7 17 7 17z" stroke="var(--gold)" fill="none" stroke-width="1.3"/><circle cx="7" cy="6.5" r="2" stroke="var(--gold)" fill="none"/></svg>Level 3/22 Banksia Avenue...</div>
    <div class="feats">
      <span><svg width="20" height="14"><rect x="1" y="1" width="18" height="12" stroke="var(--gold)" fill="none" stroke-width="1.3"/><path d="M1 8h18" stroke="var(--gold)"/></svg>2</span>
      <span><svg width="20" height="16"><path d="M1 8h18v3a4 4 0 01-4 4H5a4 4 0 01-4-4zM4 8V2h4" stroke="var(--gold)" fill="none" stroke-width="1.3"/></svg>2</span>
      <span><svg width="26" height="14"><path d="M1 10V7l4-1 4-4h8l5 4 3 1v3H1z" stroke="var(--gold)" fill="none" stroke-width="1.3"/><circle cx="7" cy="11" r="2" fill="#fff" stroke="var(--gold)"/><circle cx="19" cy="11" r="2" fill="#fff" stroke="var(--gold)"/></svg>1</span>
    </div>
    <h4>Next Inspirition:</h4>
    <div class="when">Sat 21st May 9:40 Am-10:00 Am</div>
    <div class="agent"><div class="avatar" role="img" aria-label="Agent portrait"></div>Mei Lin
      <div class="tools"><svg width="18" height="18"><circle cx="9" cy="9" r="7" stroke="#333" fill="none" stroke-width="1.3"/><path d="M9 5v4l3 2" stroke="#333" fill="none" stroke-width="1.3"/></svg><svg width="18" height="18"><path d="M2 6V2h4M12 2h4v4M16 12v4h-4M6 16H2v-4M2 2l5 5M16 2l-5 5M16 16l-5-5M2 16l5-5" stroke="#333" fill="none" stroke-width="1.3"/></svg><svg width="20" height="18"><rect x="1" y="3" width="18" height="12" stroke="#333" fill="none" stroke-width="1.3"/><path d="M1 3l9 7 9-7" stroke="#333" fill="none" stroke-width="1.3"/></svg></div>
    </div>
  </article>

  <article class="card" style="left:800px">
    <div class="card-photo" role="img" aria-label="Photo of a suburban home with a double garage and trees" style="background:linear-gradient(170deg,#5e94d0 0%,#8aa06a 45%,#c8b9a4 100%)">
      <svg class="star" width="20" height="20" viewBox="0 0 24 24"><path d="M12 2l3 6.5 7 .8-5.2 4.8 1.5 7L12 17.6 5.7 21l1.5-7L2 9.3l7-.8z" fill="var(--gold)"/></svg>
      <span class="badge">On Sale</span>
      <svg class="arrow-l" width="10" height="20"><path d="M9 1L1 10l8 9" stroke="#fff" fill="none" stroke-width="1.5"/></svg>
      <svg class="arrow-r" width="10" height="20"><path d="M1 1l8 9-8 9" stroke="#fff" fill="none" stroke-width="1.5"/></svg>
      <span class="price">$5,00,000+</span>
    </div>
    <h3>Gungahlin</h3>
    <div class="addr"><svg width="14" height="18" viewBox="0 0 14 18"><path d="M7 17S1 10 1 6.5a6 6 0 0112 0C13 10 7 17 7 17z" stroke="var(--gold)" fill="none" stroke-width="1.3"/><circle cx="7" cy="6.5" r="2" stroke="var(--gold)" fill="none"/></svg>Level 3/22 Banksia Avenue...</div>
    <div class="feats">
      <span><svg width="20" height="14"><rect x="1" y="1" width="18" height="12" stroke="var(--gold)" fill="none" stroke-width="1.3"/><path d="M1 8h18" stroke="var(--gold)"/></svg>2</span>
      <span><svg width="20" height="16"><path d="M1 8h18v3a4 4 0 01-4 4H5a4 4 0 01-4-4zM4 8V2h4" stroke="var(--gold)" fill="none" stroke-width="1.3"/></svg>2</span>
      <span><svg width="26" height="14"><path d="M1 10V7l4-1 4-4h8l5 4 3 1v3H1z" stroke="var(--gold)" fill="none" stroke-width="1.3"/><circle cx="7" cy="11" r="2" fill="#fff" stroke="var(--gold)"/><circle cx="19" cy="11" r="2" fill="#fff" stroke="var(--gold)"/></svg>1</span>
    </div>
    <h4>Next Inspirition:</h4>
    <div class="when">Sat 21st May 9:40 Am-10:00 Am</div>
    <div class="agent"><div class="avatar" role="img" aria-label="Agent portrait"></div>Mei Lin
      <div class="tools"><svg width="18" height="18"><circle cx="9" cy="9" r="7" stroke="#333" fill="none" stroke-width="1.3"/><path d="M9 5v4l3 2" stroke="#333" fill="none" stroke-width="1.3"/></svg><svg width="18" height="18"><path d="M2 6V2h4M12 2h4v4M16 12v4h-4M6 16H2v-4M2 2l5 5M16 2l-5 5M16 16l-5-5M2 16l5-5" stroke="#333" fill="none" stroke-width="1.3"/></svg><svg width="20" height="18"><rect x="1" y="3" width="18" height="12" stroke="#333" fill="none" stroke-width="1.3"/><path d="M1 3l9 7 9-7" stroke="#333" fill="none" stroke-width="1.3"/></svg></div>
    </div>
  </article>

  <div class="btn btn-gold" style="top:706px;left:551px;width:98px;height:34px">View More</div>
</section>

<section class="why">
  <div class="why-photo" role="img" aria-label="Photo of a handshake over a desk with documents and a small model house"></div>
  <div class="why-panel">
    <div class="label">Services</div>
    <h2 class="h2">Why choose us?</h2>
    <p>Lorem Ipsum is simply dummy text of the printing and typesetting industry. Lorem Ipsum has been the industry's standard dummy text ever since the 1500s, when an unknown printer took a galley of type and scrambled it to make a type specimen book. It has survived not only five centuries, but also the leap into electronic typesetting, remaining essentially unchanged. It was popularised in the 1960s with the release of Letraset sheets containing Lorem Ipsum passages, and more recently with desktop publishing</p>
    <div class="btn btn-gold" style="top:320px;left:43px;width:99px;height:36px;border:1.5px solid #fff">Read More</div>
  </div>
</section>

<section class="testi">
  <div class="testi-left">
    <div class="quote">&ldquo;</div>
    <p>They are a greatly professional, organized and experienced team with extensive knowledge and understanding of the local market. My husband and I were provided with excellent feedback in a simple language we could understand and advice throughout the house journey and we were very pleased with the results. We highly recommend Ferndale property group to anyone buying, selling or in need of property management in the local area."</p>
    <div class="name">Hannah Cole</div>
    <div class="testi-nav"><svg width="12" height="24"><path d="M11 1L1 12l10 11" stroke="var(--navy)" fill="none" stroke-width="1.6"/></svg><svg width="12" height="24"><path d="M1 1l10 11-10 11" stroke="var(--navy)" fill="none" stroke-width="1.6"/></svg></div>
  </div>
  <div class="testi-right">
    <div class="center label" style="top:142px">Our Testimonials</div>
    <h2 class="center h2" style="top:170px;line-height:38px">What Our People Saying<br>About Us</h2>
  </div>
</section>

<section class="blog">
  <div class="center label" style="top:85px">Blog</div>
  <h2 class="center h2" style="top:115px">Our Latest News</h2>
  <article class="post" style="left:60px">
    <div class="post-photo" role="img" aria-label="Photo of a gabled two-storey house with timber cladding" style="background:linear-gradient(170deg,#dfe6ec 0%,#b9b4ad 55%,#6c6a66 100%)"><div class="date">15<span>jun</span></div></div>
    <h3>Lorem Ipsum is simply dummy text</h3>
    <p>Lorem Ipsum is simply dummy text of the printing and typesetting industry.</p>
    <span class="read">Read More &rsaquo;</span>
  </article>
  <article class="post" style="left:431px">
    <div class="post-photo" role="img" aria-label="Photo of a modern house with a lit pool at dusk" style="background:linear-gradient(170deg,#7f97b3 0%,#4b5a6b 50%,#c99a5e 80%,#3c4e60 100%)"><div class="date">15<span>jun</span></div></div>
    <h3>Lorem Ipsum is simply dummy text</h3>
    <p>Lorem Ipsum is simply dummy text of the printing and typesetting industry.</p>
    <span class="read">Read More &rsaquo;</span>
  </article>
  <article class="post" style="left:800px">
    <div class="post-photo" role="img" aria-label="Photo of a terrace house with a green facade and front hedge" style="background:linear-gradient(170deg,#e8e8e4 0%,#55675c 45%,#2f4a33 100%)"><div class="date">15<span>jun</span></div></div>
    <h3>Lorem Ipsum is simply dummy text</h3>
    <p>Lorem Ipsum is simply dummy text of the printing and typesetting industry.</p>
    <span class="read">Read More &rsaquo;</span>
  </article>
  <div class="btn btn-gold" style="top:531px;left:551px;width:98px;height:35px">View More</div>
</section>

<section class="contact">
  <div class="map" role="img" aria-label="Street map of Gungahlin showing the office location"></div>
  <form class="touch">
    <h2>Get In Touch</h2>
    <div class="input" style="top:90px;left:67px;width:228px">First Name*</div>
    <div class="input" style="top:90px;left:311px;width:228px">Last Name*</div>
    <div class="input" style="top:138px;left:67px;width:228px">E-mail*</div>
    <div class="input" style="top:138px;left:311px;width:228px">Phone No.*</div>
    <div class="input" style="top:186px;left:67px;width:472px;height:112px">Massage*</div>
    <div class="btn btn-outline" style="top:323px;left:67px;width:114px;height:37px">Send E-mail</div>
  </form>
</section>

<footer class="footer">
  <div class="logo" style="top:46px;left:61px">
    <div class="logo-mark" style="border-color:#fff;width:50px;height:50px"></div>
    <div><div class="logo-name" style="color:#fff">Ferndale</div><div class="logo-sub" style="color:#fff">PropertyGroup</div></div>
  </div>
  <p class="abs" style="top:126px;left:61px;width:210px;font-size:12.5px;line-height:21px">Lorem ipsum dolor sit amet, consectetur adipiscing elit, sed do eiusmod tempor...</p>
  <h5 style="left:329px">Site Map</h5>
  <ul><li>Home</li><li>About Us</li><li>Leasing</li><li>Buy</li><li>Sell</li><li>Our Team</li><li>Blog</li><li>Contact Us</li></ul>
  <h5 style="left:613px">Contact Us</h5>
  <div class="contact-line" style="top:86px"><svg width="20" height="20" viewBox="0 0 20 20"><path d="M10 14S5 9 5 6a5 5 0 0110 0c0 3-5 8-5 8z" stroke="#fff" fill="none" stroke-width="1.3"/><ellipse cx="10" cy="16" rx="8" ry="3" stroke="#fff" fill="none"/></svg><span>27 Banksia Ave, Gungahlin<br>, ACT, 2912</span></div>
  <div class="contact-line" style="top:138px"><svg width="20" height="20" viewBox="0 0 20 20"><path d="M3 2h4l2 5-3 2c1 2 3 4 5 5l2-3 5 2v4c-9 0-15-6-15-15z" stroke="#fff" fill="none" stroke-width="1.3"/></svg><span style="font-weight:600;line-height:23px">02 6100 2381<br>02 6100 2395</span></div>
  <div class="contact-line" style="top:190px"><svg width="20" height="16"><rect x="1" y="2" width="18" height="12" stroke="#fff" fill="none" stroke-width="1.3"/><path d="M1 2l9 7 9-7" stroke="#fff" fill="none" stroke-width="1.3"/></svg><span>info@ferndaleestate.com.au</span></div>
  <h5 style="left:889px">Follow On Us</h5>
  <div class="social"><span class="on" aria-label="Social profile"></span><span aria-label="Social profile"></span><span aria-label="Social profile"></span><span aria-label="Social profile"></span></div>
</footer>
<div class="bottom"><span>2022© Ferndale Properties. All right reserved.</span><div class="links"><span>Privacy</span><span>Complaint Handling &amp; Dispute Resolution</span><span>Due Diligence Checklist</span></div></div>
</body>
</html>
```